We need a new business card that reflects who we are. Professional, classy, modern, and service ori

We need a business card design for a window coverings design company in Kansas City called Bright Lane Interiors. We offer professional, modern, and high quality window covering products. We are looking to portray an image of a big, national franchise. We are a 5 location (with showrooms) business with 10 professional designers and 4 professional installers. These cards will be used with Thank you cards, given to realtors, and asked for referrals with.

Target Market(s)

Kansas City

Industry/Entity Type

Business

Contact Information for Business Card

We would like our card to look clean and simple on the front, featuring our logo and Marlow Fenwick's. Our designers' phone numbers and emails should be displayed as well as their title.

Font styles to use
Sans Serif

Colors

Designer to choose colors to be used in the design.

Requirements
Must have
• Front - Logos, name, phone number, email address
• Back - Showroom locations, social media? Appt date/time?
Nice to have
• I would like a clean and modern look (not contemporary. I like a white background, but I am open to ideas. Looking for a "National chain" look for a small business.
Should not have
• Too much busyness.

```html
<!DOCTYPE html>
<html lang="en">
<head>
<meta charset="utf-8">
<title>Bright Lane Interiors – Business Card</title>
<link rel="stylesheet" href="https://fonts.googleapis.com/css2?family=Roboto:wght@400;500;700&family=Roboto+Condensed:wght@400;700&family=Cormorant+Garamond:wght@500&display=swap">
<style>
  :root {
    --backdrop: #5b4738;
    --card: #f1f1f1;
    --ink: #0b0b0b;
    --red: #c9393f;
    --grey: #555a60;
    --slate: #5f6a75;
    --white: #ffffff;
  }
  * { box-sizing: border-box; margin: 0; padding: 0; }
  html, body { width: 1200px; height: 960px; overflow: hidden; }
  body { background: var(--backdrop); font-family: "Roboto", Arial, sans-serif; position: relative; }

  .card { position: absolute; width: 600px; height: 342px; background: var(--card); overflow: hidden; box-shadow: 2px 3px 6px rgba(0,0,0,.35); }
  .card--front { left: 322px; top: 108px; }
  .card--back { left: 320px; top: 493px; }

  .front-panel { position: absolute; inset: 0; }

  .brand { position: absolute; left: 44px; top: 108px; }
  .brand-name { display: flex; align-items: center; gap: 10px; font-size: 24px; font-weight: 500; color: var(--ink); letter-spacing: .2px; }
  .brand-mark { width: 16px; height: 16px; background: var(--red); flex: none; }
  .brand-tagline { margin-top: 8px; font-family: "Cormorant Garamond", Georgia, serif; font-size: 14px; color: var(--ink); }

  .person { position: absolute; right: 30px; top: 198px; text-align: right; color: var(--white); }
  .person-name { font-family: "Roboto Condensed", Arial, sans-serif; font-weight: 700; font-size: 25px; color: var(--red); line-height: 1; }
  .person-title { font-weight: 500; font-size: 15px; margin-top: 6px; letter-spacing: .3px; }
  .contact-list { list-style: none; margin-top: 22px; font-size: 14.5px; line-height: 19.5px; }
  .contact-list li { display: flex; justify-content: flex-end; align-items: center; gap: 8px; }
  .contact-icon { width: 14px; height: 14px; fill: var(--red); flex: none; }

  .partner { position: absolute; top: 40px; left: 0; right: 0; text-align: center; font-weight: 700; font-size: 15px; color: var(--slate); }

  .appointments { position: absolute; left: 82px; top: 80px; width: 430px; list-style: none; }
  .appointment { display: flex; align-items: baseline; height: 45.5px; color: var(--red); font-size: 17px; }
  .appointment .fill { display: inline-block; height: 0; border-bottom: 1.5px dotted var(--grey); margin: 0 2px 0 4px; }
  .appointment .fill--date { width: 166px; }
  .appointment .fill--time { width: 104px; }
  .appointment .meridiem { font-size: 13px; margin-left: 4px; }

  .showrooms { position: absolute; top: 260px; left: 0; right: 0; text-align: center; }
  .showrooms-title { font-weight: 700; font-size: 15px; color: var(--red); letter-spacing: .2px; }
  .showrooms-list { font-family: "Roboto Condensed", Arial, sans-serif; font-size: 14px; color: var(--grey); margin-top: 4px; }
  .social { display: flex; justify-content: center; gap: 3px; margin-top: 6px; }
  .social span { width: 20px; height: 20px; border-radius: 50%; background: var(--red); }
</style>
</head>
<body>

<section class="card card--front" aria-label="Business card front">
  <svg class="front-panel" viewBox="0 0 600 342" width="600" height="342" aria-hidden="true">
    <path fill="var(--ink)" d="M0,300 Q260,345 600,62 L600,342 L0,342 Z"/>
    <path fill="none" stroke="var(--red)" stroke-width="3" d="M0,284 Q250,326 600,44"/>
  </svg>

  <div class="brand">
    <div class="brand-name"><span class="brand-mark"></span>Bright Lane Interiors</div>
    <div class="brand-tagline">Window Shades, Shutters, Drapes &amp; Home Accents</div>
  </div>

  <div class="person">
    <div class="person-name">EVAN CARTER</div>
    <div class="person-title">DESIGNER</div>
    <ul class="contact-list">
      <li>913.555.0148
        <svg class="contact-icon" viewBox="0 0 24 24"><path d="M6.6 10.8a15 15 0 0 0 6.6 6.6l2.2-2.2a1 1 0 0 1 1-.25 11.4 11.4 0 0 0 3.6.57 1 1 0 0 1 1 1V20a1 1 0 0 1-1 1A17 17 0 0 1 3 4a1 1 0 0 1 1-1h3.5a1 1 0 0 1 1 1c0 1.25.2 2.45.57 3.6a1 1 0 0 1-.25 1Z"/></svg>
      </li>
      <li>info@brightlaneinteriors.com
        <svg class="contact-icon" viewBox="0 0 24 24"><path d="M2 5h20v14H2Z"/><path d="M2 5l10 8 10-8" fill="none" stroke="var(--ink)" stroke-width="2"/></svg>
      </li>
      <li>www.brightlaneinteriors.com
        <svg class="contact-icon" viewBox="0 0 24 24"><circle cx="12" cy="12" r="10"/><path d="M2 12h20M12 2c3 3 3 17 0 20M12 2c-3 3-3 17 0 20" fill="none" stroke="var(--ink)" stroke-width="1.6"/></svg>
      </li>
    </ul>
  </div>
</section>

<section class="card card--back" aria-label="Business card back">
  <div class="partner">Marlow Fenwick</div>

  <ul class="appointments">
    <li class="appointment">Date :<span class="fill fill--date"></span>Time :<span class="fill fill--time"></span><span class="meridiem">AM/PM</span></li>
    <li class="appointment">Date :<span class="fill fill--date"></span>Time :<span class="fill fill--time"></span><span class="meridiem">AM/PM</span></li>
    <li class="appointment">Date :<span class="fill fill--date"></span>Time :<span class="fill fill--time"></span><span class="meridiem">AM/PM</span></li>
    <li class="appointment">Date :<span class="fill fill--date"></span>Time :<span class="fill fill--time"></span><span class="meridiem">AM/PM</span></li>
  </ul>

  <div class="showrooms">
    <div class="showrooms-title">SHOWROOM LOCATIONS</div>
    <div class="showrooms-list">ASHBY | MAPLE RIDGE | CEDAR BLUFF | NORTH CREST | PORT ELLING</div>
    <div class="social" aria-label="Social media links"><span></span><span></span><span></span><span></span></div>
  </div>
</section>

</body>
</html>
```